Wealth Education Business Needs Sharp Business Card Design

We need a business card design for a recently launched investor education business called Harbor Crest.

The final design should promote security, empowerment, self improvement and financial gain. The card will ideally promote the stature of the business.

For more information and colours please visit harborcrest.com.au

Target Market(s)

Corporate executives and high net worth individuals

Industry/Entity Type

Education

Contact Information for Business Card

```html
<!DOCTYPE html>
<html lang="en">
<head>
<meta charset="utf-8">
<title>Harbor Crest – Business Card</title>
<link rel="stylesheet" href="https://fonts.googleapis.com/css2?family=Lato:wght@400;700&display=swap">
<style>
  :root {
    --stage: #3b3b3c;
    --navy: #1f2c42;
    --navy-deep: #1a2538;
    --teal: #1a9a98;
    --paper: #ffffff;
    --ink: #3a3a3c;
    --name-ink: #1f2c42;
    --front-text: #ffffff;
  }
  * { margin: 0; padding: 0; box-sizing: border-box; }
  html, body {
    width: 1200px; height: 960px; overflow: hidden;
    background: var(--stage);
    font-family: "Lato", Arial, sans-serif;
  }
  .card {
    position: absolute; left: 270px; width: 645px; height: 369px;
    overflow: hidden;
  }
  .card-front {
    top: 83px;
    background: linear-gradient(180deg, var(--navy) 0%, var(--navy-deep) 100%);
  }
  .card-back { top: 507px; background: var(--paper); }

  .brand-name {
    position: absolute; white-space: nowrap;
    font-weight: 400; text-transform: uppercase;
    letter-spacing: 4px; font-size: 31px; line-height: 1;
  }
  .card-front .brand-name {
    color: var(--front-text);
    left: 215px; top: 157px; transform: translateX(-50%);
  }
  .card-front .web {
    position: absolute; left: 215px; top: 216px; transform: translateX(-50%);
    color: var(--front-text); font-size: 15px; letter-spacing: 0.2px;
  }

  .swoosh { position: absolute; left: 0; top: 0; }

  .card-back .brand-name {
    color: var(--ink);
    left: 457px; top: 66px; transform: translateX(-50%);
  }
  .person { position: absolute; left: 57px; top: 238px; }
  .person-name { font-size: 19px; font-weight: 700; color: var(--name-ink); }
  .person-role { font-size: 15px; color: var(--ink); margin-top: 1px; }

  .address {
    position: absolute; left: 309px; top: 189px;
    font-size: 15px; line-height: 19px; color: var(--ink); font-style: normal;
  }
  .contacts {
    position: absolute; left: 307px; top: 240px; list-style: none;
    font-size: 15px; color: var(--ink);
  }
  .contacts li { display: flex; align-items: center; height: 20.7px; }
  .contacts svg { width: 16px; height: 16px; margin-right: 13px; fill: var(--navy); }
</style>
</head>
<body>
  <section class="card card-front" aria-label="Card front">
    <div class="brand-name">Harbor Crest</div>
    <div class="web">www.<strong>harborcrest</strong>.com.au</div>
  </section>

  <section class="card card-back" aria-label="Card back">
    <svg class="swoosh" width="645" height="369" viewBox="0 0 645 369" aria-hidden="true">
      <path d="M0,0 H268 C150,28 45,92 0,165 Z" fill="var(--navy)"/>
      <path d="M0,228 C28,120 130,42 282,0 H276 C150,32 45,98 0,182 Z" fill="var(--teal)"/>
    </svg>

    <div class="brand-name">Harbor Crest</div>

    <div class="person">
      <div class="person-name">Daniel Ashford</div>
      <div class="person-role">Founder &amp; CEO</div>
    </div>

    <address class="address">Level 4, 72 Ashbury Lane<br>Southbank VIC 3006</address>

    <ul class="contacts">
      <li><svg viewBox="0 0 16 16"><path d="M1 6c0-2 3-3.5 7-3.5S15 4 15 6v1.5h-3.5V6H4.5v1.5H1z M4 8h8l2 5H2z"/></svg>1300.555.018</li>
      <li><svg viewBox="0 0 16 16"><path d="M4.5 0h7a1 1 0 0 1 1 1v14a1 1 0 0 1-1 1h-7a1 1 0 0 1-1-1V1a1 1 0 0 1 1-1zm.5 2v10h6V2zm3 11a1 1 0 1 0 0 2 1 1 0 0 0 0-2z"/></svg>0000.000.000</li>
      <li><svg viewBox="0 0 16 16"><path d="M1 3h14v10H1zm1.5 1.5v.3L8 9l5.5-4.2v-.3zm0 2.2v4.8h11V6.7L8 11z"/></svg>support@harborcrest.com.au</li>
      <li><svg viewBox="0 0 16 16"><path d="M8 0a8 8 0 1 0 0 16A8 8 0 0 0 8 0zm-.7 1.6V4.3H5.1c.5-1.4 1.3-2.4 2.2-2.7zm1.4 0c.9.3 1.7 1.3 2.2 2.7H8.7zM3.9 2.8c-.2.5-.4 1-.6 1.5H2.4c.4-.6.9-1.1 1.5-1.5zm8.2 0c.6.4 1.1.9 1.5 1.5h-.9c-.2-.5-.4-1-.6-1.5zM1.7 5.7h1.3c-.1.6-.1 1.2-.1 1.6H1.4c0-.6.1-1.1.3-1.6zm3 0h2.6v1.6H4.4c0-.6.1-1.1.3-1.6zm4 0h2.6c.2.5.3 1 .3 1.6H8.7zm4.2 0h1.4c.2.5.3 1 .3 1.6h-1.6c0-.4 0-1-.1-1.6zM1.4 8.7h1.5c0 .5 0 1 .1 1.6H1.7c-.2-.5-.3-1-.3-1.6zm3 0h2.9v1.6H4.7c-.2-.5-.3-1-.3-1.6zm4.3 0h2.9c0 .6-.1 1.1-.3 1.6H8.7zm4.4 0h1.5c0 .6-.1 1.1-.3 1.6H13c.1-.6.1-1.1.1-1.6zM2.4 11.7h.9c.2.5.4 1 .6 1.5-.6-.4-1.1-.9-1.5-1.5zm2.7 0h2.2v2.7c-.9-.3-1.7-1.3-2.2-2.7zm3.6 0h2.2c-.5 1.4-1.3 2.4-2.2 2.7zm4 0h.9c-.4.6-.9 1.1-1.5 1.5.2-.5.4-1 .6-1.5z"/></svg>www.harborcrest.com.au</li>
    </ul>
  </section>
</body>
</html>
```